Heritage Hollow Business Cards

Require a business card design. <br/><br/>Needs to include logo (either round or long version) plus these details:<br/>Maya Torvell<br/>Heritage Hollow<br/>maya@kelvadtrading.com.au<br/>02 6481 7395<br/>PO Box Glenwarra NSW 2791<br/>www.heritagehollow.com.au<br/><br/>I need in an editable format so that I can create for multiple staff members. <br/><br/>

Target Market(s)

We are an online store selling renovation products to home owners are builders. Looking for a classic classy design.

Industry/Entity Type

Home And Garden

Contact Information for Business Card

Maya Torvell
Heritage Hollow
maya@kelvadtrading.com.au
02 6481 7395
PO Box Glenwarra NSW 2791
www.heritagehollow.com.au

Colors

Designer to choose colors to be used in the design.

Requirements
Must have
• Must include Logo.

```html
<!DOCTYPE html>
<html lang="en">
<head>
<meta charset="utf-8">
<title>Heritage Hollow Business Cards</title>
<link rel="stylesheet" href="https://fonts.googleapis.com/css2?family=Alegreya:wght@400&family=Roboto:wght@400;500;700&display=swap">
<style>
  :root {
    --backdrop: #dcdde1;
    --card-dark: #0b0b0b;
    --card-dark-edge: #050505;
    --card-light: #ffffff;
    --ink: #1a1a1a;
    --ink-soft: #333333;
    --emboss: #5a5a5a;
  }
  * { margin: 0; padding: 0; box-sizing: border-box; }
  html, body { width: 1200px; height: 1200px; overflow: hidden; }
  body { background: var(--backdrop); position: relative; font-family: "Roboto", sans-serif; }

  .card {
    position: absolute;
    left: 269px;
    width: 663px;
    height: 379px;
    border-radius: 22px;
    overflow: hidden;
  }
  .card--front {
    top: 178px;
    background: radial-gradient(ellipse at 40% 35%, #1c1c1c 0%, var(--card-dark) 55%, var(--card-dark-edge) 100%);
  }
  .card--back { top: 643px; background: var(--card-light); }

  .front-wordmark {
    position: absolute;
    left: 0; right: 0;
    top: 200px;
    text-align: center;
    font-family: "Alegreya", serif;
    font-size: 44px;
    color: var(--emboss);
    letter-spacing: 0.5px;
  }

  .brand-seal {
    position: absolute;
    left: 42px; top: 26px;
    width: 190px; height: 190px;
    border: 1px solid var(--ink);
    border-radius: 50%;
  }
  .brand-name {
    position: absolute;
    left: 68px; top: 126px;
    font-family: "Alegreya", serif;
    font-size: 27px;
    line-height: 26px;
    color: var(--ink);
  }

  .person-name {
    position: absolute;
    left: 68px; top: 262px;
    font-family: "Alegreya", serif;
    font-size: 24px;
    color: var(--ink-soft);
    letter-spacing: 0.3px;
  }

  .contact {
    position: absolute;
    left: 381px; top: 270px;
    height: 90px;
    border-left: 1.5px solid var(--ink);
    padding-left: 12px;
  }
  .contact__company {
    font-size: 16px;
    font-weight: 500;
    color: var(--ink);
    line-height: 18px;
    margin-top: -1px;
    margin-bottom: 2px;
  }
  .contact__line {
    display: flex;
    align-items: center;
    gap: 5px;
    font-size: 12.5px;
    color: var(--ink-soft);
    line-height: 18.5px;
  }
  .contact__line svg { width: 9px; height: 9px; flex: none; fill: var(--ink); }
  .contact__line b { font-weight: 700; }
</style>
</head>
<body>

<section class="card card--front" aria-label="Card front">
  <div class="front-wordmark">Heritage Hollow</div>
</section>

<section class="card card--back" aria-label="Card back">
  <div class="brand-seal"></div>
  <div class="brand-name">Heritage<br>Hollow</div>

  <div class="person-name">MAYA TORVELL</div>

  <div class="contact">
    <div class="contact__company">HERITAGE HOLLOW</div>
    <div class="contact__line">
      <svg viewBox="0 0 10 10"><path d="M5 0a3.4 3.4 0 0 0-3.4 3.4C1.6 6 5 10 5 10s3.4-4 3.4-6.6A3.4 3.4 0 0 0 5 0zm0 4.8a1.4 1.4 0 1 1 0-2.8 1.4 1.4 0 0 1 0 2.8z"/></svg>
      <span>PO Box Glenwarra NSW 2791</span>
    </div>
    <div class="contact__line">
      <svg viewBox="0 0 10 10"><path d="M2.2 0.5l1.6 2-1 1.1c.6 1.4 1.6 2.4 3 3l1.1-1 2 1.6-1 1.8C4.5 9 1 5.5 1.1 1.5z"/></svg>
      <span>02 6481 7395</span>
    </div>
    <div class="contact__line">
      <svg viewBox="0 0 10 10"><path d="M0 2h10v6H0zM0.8 2.6L5 5.6l4.2-3v0.8L5 6.4 0.8 3.4z" fill-rule="evenodd"/></svg>
      <span>maya@kelvadtrading.com.au</span>
    </div>
    <div class="contact__line">
      <svg viewBox="0 0 10 10"><circle cx="5" cy="5" r="4.3" fill="none" stroke="#1a1a1a" stroke-width="0.9"/><path d="M0.7 5h8.6M5 0.7v8.6" stroke="#1a1a1a" stroke-width="0.7"/><ellipse cx="5" cy="5" rx="2" ry="4.3" fill="none" stroke="#1a1a1a" stroke-width="0.7"/></svg>
      <span>www.<b>heritagehollow</b>.com.au</span>
    </div>
  </div>
</section>

</body>
</html>
```